Looking for someone to design a business card for my plumbing business Quandor Plumbing Solutions I want the background also to be black, must attract clients. If possible I want the front to be the logo and the back to show maybe the details.

Target Market(s)

Clients

Industry/Entity Type

Plumbing maintenance

Contact Information for Business Card

Name: Felix, Contact: 0461 539 207, Email: quandorplumbingsolutions@mailbrook.example, Licence number 728093K

Font styles to use
Other font styles liked:
• as per logo maybe?

Colors

Designer to choose colors to be used in the design.

Requirements
Nice to have
• stating the service I provide, emergency plumbing, plumbing maintenance, drainage maintenance, block sewer and stormwater, camera and locating.

```html
<!DOCTYPE html>
<html lang="en">
<head>
<meta charset="utf-8">
<title>Quandor Plumbing Solutions — Business Card</title>
<link rel="stylesheet" href="https://fonts.googleapis.com/css2?family=Montserrat:wght@400;500;700;800&display=swap">
<style>
  :root {
    --backdrop: #d9d8d6;
    --card: #1f1f1f;
    --edge: #3f8fd8;
    --accent: #4a93d6;
    --text: #f2f2f2;
    --ghost: #2c2c2c;
    --ghost-light: #3a3a3a;
  }
  * { margin: 0; padding: 0; box-sizing: border-box; }
  html, body { width: 1200px; height: 801px; overflow: hidden; }
  body {
    background: var(--backdrop);
    font-family: "Montserrat", Arial, sans-serif;
    position: relative;
  }
  .card {
    position: absolute;
    width: 540px;
    height: 309px;
    background: var(--card);
    border-bottom: 4px solid var(--edge);
    box-shadow: 0 14px 30px rgba(0,0,0,0.25);
    overflow: hidden;
  }
  .card--details { left: 40px; top: 246px; }
  .card--brand { left: 620px; top: 246px; }

  /* details side */
  .brand-mark {
    position: absolute;
    top: 30px;
    right: 34px;
    display: flex;
    align-items: center;
    gap: 10px;
  }
  .brand-mark__dot {
    width: 26px; height: 26px;
    border-radius: 50%;
    background: var(--accent);
  }
  .brand-mark__name {
    color: var(--text);
    font-weight: 800;
    font-size: 17px;
    letter-spacing: 0.5px;
    text-transform: uppercase;
    line-height: 1.1;
  }
  .person { position: absolute; left: 34px; top: 90px; }
  .person__name {
    color: var(--accent);
    font-weight: 800;
    font-size: 22px;
    letter-spacing: 0.5px;
    text-transform: uppercase;
    line-height: 1;
  }
  .person__role { color: var(--text); font-size: 12px; font-weight: 500; margin-top: 2px; }

  .contact { position: absolute; left: 34px; top: 148px; list-style: none; }
  .contact li {
    color: var(--text);
    font-size: 11.5px;
    line-height: 17px;
    display: flex;
    align-items: center;
    gap: 7px;
  }
  .contact svg { width: 10px; height: 10px; flex: none; }
  .contact .contact__licence { padding-left: 0; }

  .services {
    position: absolute;
    left: 34px;
    top: 238px;
    right: 24px;
    list-style: none;
    display: flex;
    flex-wrap: wrap;
    column-gap: 10px;
    row-gap: 2px;
  }
  .services li {
    color: var(--text);
    font-size: 11.5px;
    line-height: 17px;
  }
  .services li::before {
    content: "•";
    color: var(--accent);
    margin-right: 6px;
  }

  /* brand side */
  .brand-large {
    position: absolute;
    left: 0; right: 0; top: 0; bottom: 0;
    display: flex;
    align-items: center;
    justify-content: center;
    gap: 16px;
  }
  .brand-large__dot {
    width: 54px; height: 54px;
    border-radius: 50%;
    background: var(--ghost);
  }
  .brand-large__name {
    color: var(--ghost-light);
    font-weight: 800;
    font-size: 30px;
    letter-spacing: 1px;
    line-height: 1.05;
    text-transform: uppercase;
  }
</style>
</head>
<body>

  <section class="card card--details" aria-label="Card back with contact details">
    <div class="brand-mark">
      <span class="brand-mark__dot"></span>
      <span class="brand-mark__name">Quandor<br>Plumbing Solutions</span>
    </div>

    <div class="person">
      <p class="person__name">Felix</p>
      <p class="person__role">Founder &amp; CEO</p>
    </div>

    <ul class="contact">
      <li class="contact__licence">Licence number 728093K</li>
      <li>
        <svg viewBox="0 0 10 10" aria-hidden="true"><path d="M2 0.5 L3.6 2.6 L2.8 3.6 Q3.8 5.8 6.2 7.1 L7.3 6.3 L9.5 7.9 L8.4 9.5 Q2.5 8.6 0.6 1.6 Z" fill="var(--accent)"/></svg>
        0461 539 207
      </li>
      <li>
        <svg viewBox="0 0 10 10" aria-hidden="true"><rect x="0.5" y="2" width="9" height="6.5" fill="var(--accent)"/><path d="M0.8 2.3 L5 5.6 L9.2 2.3" stroke="var(--card)" stroke-width="0.9" fill="none"/></svg>
        quandorplumbingsolutions@mailbrook.example
      </li>
      <li>
        <svg viewBox="0 0 10 10" aria-hidden="true"><circle cx="5" cy="5" r="4.6" fill="var(--accent)"/></svg>
        @QuandorPlumbingSolutions
      </li>
    </ul>

    <ul class="services">
      <li>Emergency plumbing</li>
      <li>Plumbing maintenance</li>
      <li>Drainage maintenance</li>
      <li>Block sewer and stormwater</li>
      <li>Camera and locating</li>
    </ul>
  </section>

  <section class="card card--brand" aria-label="Card front with brand name">
    <div class="brand-large">
      <span class="brand-large__dot"></span>
      <span class="brand-large__name">Quandor<br>Plumbing Solutions</span>
    </div>
  </section>

</body>
</html>
```